Website for Boutique Property Consultancy in UK

We are looking to designing a website for our Property Consultancy Services that follows a minimalistic clean style that is also bold and intriguing.
The website will be based on one landing page and a link to Netlink Page and email link.

Dominant features will be the company logo or icon and colours.

Brand colours provided for guidance.

Looking to achieve a minimalistic clean style that is also bold and intriguing.

"Updated"
Page 1 - Landing Page with the Hyperlinks to Pick a Service, Training Portal and Quill Meadow Portal. example landing page https://brantwistle.co.uk/

Page 2 - Shows all the Services and Sectors

Target Market(s)

Occupier Clients, Tech Companies, Property Developers, Infrastructure Clients and Major Consultants

Industry/Entity Type

Construction

Coding

Coded - Design and coding required

Number of Pages Required

2 page

Font styles to use
Other font styles liked:
• Century Gothic or Futuris (Headings)

Colors
0054AA
0677BA
7BADD7
CADEEF
E8F1F8
00AB8E
00BBA5
67D7C9
C6EFE9
E9F9F6

Requirements
Must have
• Company Logo, link to enquiry and Netlink

```html
<!DOCTYPE html>
<html lang="en">
<head>
<meta charset="utf-8">
<title>Ferrow Lane — Landing Page</title>
<link rel="stylesheet" href="https://fonts.googleapis.com/css2?family=Questrial&display=swap">
<style>
  :root {
    --navy: #131338;
    --navy-deep: #09042d;
    --green: #1ec075;
    --orange: #f37726;
    --white: #ffffff;
    --paper: #e9e9eb;
    --muted: #d9d9e6;
  }
  * { box-sizing: border-box; margin: 0; padding: 0; }
  html, body {
    width: 888px; height: 1200px; overflow: hidden;
    background: var(--paper);
    font-family: "Questrial", "Century Gothic", sans-serif;
  }
  .stage {
    position: absolute; left: 0; top: 322px;
    width: 888px; height: 555px; overflow: hidden;
  }
  .landing {
    position: absolute; left: 0; top: 0;
    width: 1129px; height: 706px;
    transform: scale(0.7865); transform-origin: 0 0;
    background: var(--navy);
    color: var(--white);
  }
  .brand {
    position: absolute; left: 72px; top: 18px;
    font-size: 19px; letter-spacing: 0.5px; color: var(--white);
    display: flex; align-items: center; gap: 8px;
  }
  .brand-dot { width: 9px; height: 9px; border-radius: 50%; background: var(--green); }
  .main-nav {
    position: absolute; left: 239px; top: 24px;
    display: flex; gap: 16px; font-size: 10.5px; list-style: none;
  }
  .main-nav a { color: var(--white); text-decoration: none; }
  .hero { position: absolute; left: 72px; top: 246px; }
  .eyebrow {
    font-size: 9.5px; letter-spacing: 3.2px; text-transform: uppercase;
    color: var(--orange);
  }
  .headline {
    margin-top: 10px; font-weight: 400; font-size: 36.5px; line-height: 43px;
    letter-spacing: 0.2px;
  }
  .headline em { font-style: normal; color: var(--green); }
  .contact-line { margin-top: 39px; font-size: 12px; color: var(--muted); }
  .contact-line a { color: var(--muted); text-decoration: none; }
  .badge { margin-top: 30px; display: block; }
  .hero-photo {
    position: absolute; left: 507px; top: 0; width: 393px; height: 706px;
    background:
      linear-gradient(160deg, rgba(255,255,255,0.55) 0%, rgba(255,255,255,0) 35%),
      linear-gradient(180deg, #cfd1d4 0%, #b7b6bd 30%, #a49ea7 55%, #cfc8cb 75%, #b9b7bd 100%);
  }
  .follow {
    position: absolute; left: 966px; top: 16px;
    display: flex; align-items: center; gap: 14px; font-size: 10.5px;
  }
  .follow-dot { width: 32px; height: 32px; border-radius: 50%; background: var(--green); display: block; }
  .sector {
    position: absolute; right: 66px; text-align: right;
    font-size: 11px; line-height: 17.5px; color: var(--muted);
  }
  .sector--tech { top: 260px; }
  .sector--infra { top: 411px; }
  .sector-rule {
    position: absolute; left: 958px; top: 352px; width: 171px; height: 1px;
    background: var(--orange);
  }
</style>
</head>
<body>
  <div class="stage">
    <section class="landing">
      <header>
        <div class="brand"><span class="brand-dot"></span>Ferrow Lane</div>
        <ul class="main-nav">
          <li><a href="#services">Pick a Service</a></li>
          <li><a href="#training">Training Portal</a></li>
          <li><a href="#portal">Quill Meadow</a></li>
        </ul>
      </header>

      <div class="hero">
        <p class="eyebrow">Welcome to Ferrow Lane</p>
        <h1 class="headline">Delivering <em>Value</em> and<br>Redefining <em>Boundaries</em></h1>
        <p class="contact-line">By Referral Only &nbsp;|&nbsp; <a href="#enquiry">Email/Netlink</a></p>
        <svg class="badge" width="70" height="28" viewBox="0 0 70 28" role="img" aria-label="Professional accreditation badge">
          <circle cx="13" cy="13" r="11" fill="none" stroke="#ffffff" stroke-width="2"/>
          <rect x="29" y="5" width="38" height="12" rx="2" fill="#ffffff"/>
          <rect x="29" y="20" width="38" height="5" fill="#ffffff"/>
        </svg>
      </div>

      <div class="hero-photo" role="img" aria-label="Photo of two construction professionals in hard hats holding plans outside a modern building"></div>

      <div class="follow">Follow Us: <a class="follow-dot" href="#network" aria-label="Professional network page"></a></div>
      <p class="sector sector--tech">Tech Companies,<br>Property Developers</p>
      <div class="sector-rule"></div>
      <p class="sector sector--infra">Infrastructure Clients<br>and Major Consultants</p>
    </section>
  </div>
</body>
</html>
```